Design a refer a friend Flyer (French & English)
Flyer Title:
Main Title: "Refer a Friend & Receive a Free Electric Toothbrush!"
Bold and clear, centered at the top.
Use a clean and modern font.
Color: White text on a vivid green background for maximum contrast and readability.
Visual Focus:
Toothbrush Image: Place a high-quality image of the Dentiva Max 300 Electric Toothbrush in the center of the flyer.
Include a small price tag with “Value of $50” near the toothbrush to highlight the reward.
Simple Message:
Text: "Refer a friend to Centre Dentaire Lac-Ombré. When they book and attend their appointment, you get a free electric toothbrush, and they receive a special gift!"
Straightforward and easy to understand.
Placed below the image of the toothbrush.
Referral Process:
3 Easy Steps:
Refer a Friend
They Book and Come to Their Appointment
Receive Your Free Electric Toothbrush
Use simple, minimal icons to visually represent each step.
Keep the steps aligned horizontally or vertically for clarity.
Call to Action:
Text: "Start Referring Today!"
Place it in a button-like design in the vivid green color with bold, white text to make it stand out.
Contact Information:
Details:
Logo of Centre Dentaire Lac-Ombré.
Address: "42 Rue Valmonde Ouest, Suite 310".
Phone Number and Website: Positioned at the bottom for easy reference.
Color Scheme:
Use a vivid green background for the entire flyer, with white accents for text and icons to maintain a fresh, clean look.
Minimal clutter, focusing on clarity and the key elements: the toothbrush, the call to action, and contact information.
Clinic : www.cdlacombre.example
Attached is the brandbook, logo and inspo I made with AI.
French text will be provided.
Thank you,
Tarin

```html
<!DOCTYPE html>
<html lang="en">
<head>
<meta charset="utf-8">
<title>Refer a Friend – Centre Dentaire Lac-Ombré</title>
<link rel="stylesheet" href="https://fonts.googleapis.com/css2?family=Montserrat:wght@500;600;700;800;900&display=swap">
<style>
  :root {
    --green: #0e7a3c;
    --green-dark: #0a4f28;
    --green-deep: #06301a;
    --green-soft: #e7f3ea;
    --red: #d8242b;
    --ink: #1b1b1b;
    --navy: #1f3f7a;
    --white: #ffffff;
    --black: #111111;
  }
  * { box-sizing: border-box; margin: 0; padding: 0; }
  html, body { width: 867px; height: 1200px; overflow: hidden; background: var(--white); }
  body { font-family: "Montserrat", Arial, sans-serif; color: var(--ink); }

  .flyer { position: relative; width: 867px; height: 1200px; background: var(--white); }
  .frame { position: absolute; inset: 14px; border: 10px solid var(--green-dark); pointer-events: none; }

  .kicker {
    position: absolute; top: 40px; left: 0; width: 100%;
    text-align: center; font-weight: 800; font-size: 33px; letter-spacing: 1.5px;
    color: var(--ink); text-transform: uppercase;
  }
  .headline {
    position: absolute; top: 118px; left: 0; width: 100%;
    text-align: center; font-weight: 900; text-transform: uppercase;
    color: var(--green); line-height: 1;
  }
  .headline .line { display: block; font-size: 66px; }
  .headline .line + .line { margin-top: 10px; }
  .free-tag {
    display: inline-block; background: var(--red); color: var(--white);
    padding: 2px 14px 4px; border: 4px solid var(--white);
    box-shadow: 0 0 0 3px var(--red); margin-right: 10px;
  }

  .message {
    position: absolute; top: 282px; left: 80px; width: 330px;
    font-size: 21px; line-height: 1.32; font-weight: 500; color: var(--ink);
  }
  .message strong { font-weight: 800; }

  .gift-box {
    position: absolute; top: 470px; left: 118px; width: 230px; height: 100px;
    border: 5px solid var(--red); border-radius: 12px; background: var(--white);
    text-align: center; font-weight: 900; font-size: 34px; line-height: 1.05;
    color: var(--red); padding-top: 14px; text-transform: uppercase;
  }
  .gift-box .ribbon { position: absolute; top: -26px; left: 50%; transform: translateX(-50%); }

  .product-panel {
    position: absolute; top: 275px; left: 560px; width: 262px; height: 760px;
    border-radius: 130px 130px 0 0;
    background: linear-gradient(180deg, #0c3a20 0%, #0f6b35 45%, #1f9a4e 75%, #dfeee3 100%);
  }

  .value-badge { position: absolute; top: 395px; left: 395px; width: 170px; height: 170px; }
  .value-badge text { font-family: "Montserrat", Arial, sans-serif; fill: var(--white); }

  .steps-title {
    position: absolute; top: 592px; left: 72px;
    font-weight: 900; font-size: 31px; color: var(--ink); text-transform: uppercase;
  }
  .steps { position: absolute; top: 645px; left: 72px; display: flex; gap: 14px; }
  .step {
    position: relative; width: 132px; height: 112px;
    border: 3px solid var(--green); border-radius: 10px; background: var(--green-soft);
    padding: 26px 8px 6px; display: flex; align-items: center; gap: 6px;
  }
  .step-label {
    position: absolute; top: -12px; left: 50%; transform: translateX(-50%);
    background: var(--green); color: var(--white); font-weight: 800; font-size: 12px;
    padding: 3px 10px; border-radius: 4px; white-space: nowrap;
  }
  .step:nth-child(2) .step-label { background: var(--navy); }
  .step:nth-child(3) .step-label { background: var(--green-dark); }
  .step-icon { flex: 0 0 24px; }
  .step-text { font-size: 12.5px; font-weight: 600; line-height: 1.2; color: var(--ink); }

  .clinic-name { position: absolute; top: 800px; left: 80px; display: flex; align-items: center; gap: 14px; }
  .clinic-name .name { font-weight: 700; font-size: 30px; color: var(--navy); line-height: 1.1; }
  .clinic-name .dot { width: 22px; height: 22px; border-radius: 50%; background: var(--navy); }

  .cta {
    position: absolute; top: 900px; left: 72px; width: 570px; height: 56px;
    background: var(--green); border-radius: 6px; color: var(--white);
    font-weight: 900; font-size: 27px; letter-spacing: 0.5px; text-transform: uppercase;
    display: flex; align-items: center; padding-left: 22px;
  }

  .contact { position: absolute; top: 990px; left: 90px; list-style: none; }
  .contact li { display: flex; align-items: center; gap: 14px; font-size: 20px; font-weight: 600; margin-bottom: 16px; }
  .contact .icon {
    width: 34px; height: 34px; border-radius: 50%; background: var(--green);
    display: flex; align-items: center; justify-content: center;
  }
</style>
</head>
<body>
<main class="flyer">
  <div class="frame"></div>

  <p class="kicker">Refer a Friend &amp; Receive a</p>
  <h1 class="headline">
    <span class="line"><span class="free-tag">Free</span>Electric</span>
    <span class="line">Tooth Brush!</span>
  </h1>

  <p class="message"><strong>Refer a friend to Centre Dentaire Lac-Ombré.</strong> When they book and attend their appointment, you get a free electric toothbrush, and they receive a</p>

  <div class="gift-box">
    <svg class="ribbon" width="70" height="40" viewBox="0 0 70 40" aria-hidden="true">
      <path d="M35 30 C20 6 4 8 8 22 C10 30 26 30 35 30 Z" fill="var(--red)"/>
      <path d="M35 30 C50 6 66 8 62 22 C60 30 44 30 35 30 Z" fill="var(--red)"/>
      <circle cx="35" cy="30" r="7" fill="var(--red)"/>
    </svg>
    Special<br>Gift!
  </div>

  <div class="product-panel" role="img" aria-label="Dentiva Max 300 electric toothbrush in black standing on a pale green podium, with a soft green glow around the brush head"></div>

  <svg class="value-badge" viewBox="0 0 170 170" aria-label="Value of $50">
    <path fill="var(--black)" d="M85 4 L100 14 L118 11 L127 27 L144 33 L145 51 L158 64 L151 81 L158 98 L145 111 L144 129 L127 135 L118 151 L100 148 L85 158 L70 148 L52 151 L43 135 L26 129 L25 111 L12 98 L19 81 L12 64 L25 51 L26 33 L43 27 L52 11 L70 14 Z" transform="translate(0,4)"/>
    <circle cx="85" cy="85" r="58" fill="none" stroke="var(--white)" stroke-width="2" opacity="0.6"/>
    <text x="85" y="72" text-anchor="middle" font-size="19" font-weight="800">VALUE OF</text>
    <text x="85" y="118" text-anchor="middle" font-size="48" font-weight="900">$50</text>
  </svg>

  <h2 class="steps-title">3 Easy Steps:</h2>
  <ol class="steps">
    <li class="step">
      <span class="step-label">STEP 1</span>
      <svg class="step-icon" width="24" height="24" viewBox="0 0 24 24" aria-hidden="true"><circle cx="9" cy="8" r="4" fill="var(--green)"/><path d="M2 21c0-4 3-7 7-7s7 3 7 7z" fill="var(--green)"/><path d="M18 8v8M14 12h8" stroke="var(--green)" stroke-width="2.4"/></svg>
      <span class="step-text">Refer a Friend</span>
    </li>
    <li class="step">
      <span class="step-label">STEP 2</span>
      <svg class="step-icon" width="24" height="24" viewBox="0 0 24 24" aria-hidden="true"><rect x="3" y="5" width="18" height="16" rx="2" fill="none" stroke="var(--navy)" stroke-width="2"/><path d="M3 10h18M8 3v4M16 3v4" stroke="var(--navy)" stroke-width="2"/><path d="M8 15l3 3 5-5" fill="none" stroke="var(--navy)" stroke-width="2"/></svg>
      <span class="step-text">They Book and Come to Their Appointment</span>
    </li>
    <li class="step">
      <span class="step-label">STEP 3</span>
      <svg class="step-icon" width="24" height="24" viewBox="0 0 24 24" aria-hidden="true"><rect x="3" y="10" width="18" height="11" rx="1" fill="var(--green-dark)"/><rect x="2" y="7" width="20" height="4" fill="var(--green)"/><path d="M12 7v14" stroke="var(--white)" stroke-width="2"/></svg>
      <span class="step-text">Receive Your Free Electric Toothbrush</span>
    </li>
  </ol>

  <div class="clinic-name">
    <span class="name">Clinique Dentaire<br>Lac-Ombré</span>
    <span class="dot"></span>
  </div>

  <div class="cta">Start Referring Today!</div>

  <ul class="contact">
    <li>
      <span class="icon"><svg width="18" height="18" viewBox="0 0 24 24" aria-hidden="true"><path d="M12 2a7 7 0 0 0-7 7c0 5 7 13 7 13s7-8 7-13a7 7 0 0 0-7-7zm0 9.5a2.5 2.5 0 1 1 0-5 2.5 2.5 0 0 1 0 5z" fill="var(--white)"/></svg></span>
      42 Rue Valmonde Ouest, Suite 310
    </li>
    <li>
      <span class="icon"><svg width="18" height="18" viewBox="0 0 24 24" aria-hidden="true"><circle cx="12" cy="12" r="9" fill="none" stroke="var(--white)" stroke-width="2"/><path d="M3 12h18M12 3c3 3 3 15 0 18M12 3c-3 3-3 15 0 18" fill="none" stroke="var(--white)" stroke-width="1.8"/></svg></span>
      www.cdlacombre.example
    </li>
  </ul>
</main>
</body>
</html>
```